BrimLO (Beer/Wine candles) Edgy Candle with a Cause

Help us to help others. BrimLo is a beautifully scented natural soy candle made using repurposed beer/ wine bottles while at the same time donating a portion of our profits to youth alcohol education programs. (1. Waste = Repurposed beer/wine bottle, 2.) BrimLO = (anti) drunk/alcohol 3.) Ed = education/prevention programs.)
We're looking for a design that is cool and bold yet elegant and appeals to women (90% of our customers.) No traditional beer label designs please.

The "BrimLO" logo should appear prominently in the design with the scent name (in a different font) "on top." (See the "Velvet Brimmed" poster attached.

Examples of actual scents: Amber Drift, Glowing Paloma, Fizzing Mock-ree. (None of the fragrances smell like beer/alcohol or wine.)

Also the ED in BrimeLO should stand out in some way.

The emphasis should not be on the recycling aspect, so no obvious recycling symbols.

We are open to different interpretations and have attached varying examples that we like.
Note: a "blackboard/chalkboard" label is an idea since this deals with education.

Note: files & fonts used in the final design should be editable so that we can add other scent names as needed.

Target Market(s)

Candle buyers, specifically women between the ages of 16-45

Requirements
Must have
• 1.)Free fonts or license fonts under $20.00 2.) fonts modified to look unique/original. 3.) Editable Scent name 4.) Burning instructions 5.) Warning Info
• Burning Instructions: Trim wick to 1/4" before each lighting. Keep free from foreign materials including wick trimmings. For an even burn, burn for at least 1 hour but not more than 4 hours at a time. Discontinue use when 1/4" of wax remains. Discard or recycle after use.
• Warning: Burn candle within sight. Keep out of reach of children and pets. Keep away from things that catch fire. Use with caution.
Nice to have
• Colored Scent Names
Should not have
• recycle symbols

```html
<!DOCTYPE html>
<html lang="en">
<head>
<meta charset="utf-8">
<title>BrimLO – Fizzing Mock-ree Label</title>
<link rel="stylesheet" href="https://fonts.googleapis.com/css2?family=Indie+Flower&family=Cabin+Sketch:wght@700&display=swap">
<style>
  :root {
    --board: #2b2d2d;
    --board-dark: #1c1e1e;
    --chalk: #ecebe4;
    --cream: #e8e4d2;
    --scent-green: #9be03a;
    --brand-red: #f0504a;
    --accent-yellow: #e7a92e;
    --grey-chalk: #b9b9b4;
  }
  html, body {
    margin: 0;
    padding: 0;
    overflow: hidden;
    background: var(--board-dark);
  }
  .label {
    position: relative;
    width: 1200px;
    height: 933px;
    overflow: hidden;
    background: radial-gradient(ellipse at 50% 45%, #383a3a 0%, var(--board) 55%, var(--board-dark) 100%);
    color: var(--chalk);
    font-family: "Indie Flower", cursive;
  }
  .label > * { position: absolute; margin: 0; }

  .warning {
    left: 30px; top: 10px; width: 268px;
    font-size: 23px; line-height: 27px;
  }
  .pointer { left: 278px; top: 130px; }

  .scent-name {
    left: 335px; top: 70px; width: 515px;
    font-size: 62px; line-height: 1.2;
    color: var(--scent-green);
    font-weight: 400; white-space: nowrap;
  }
  .scent-rule { left: 325px; top: 196px; }

  .ingredients {
    left: 860px; top: 18px; width: 330px;
    font-size: 26px; line-height: 41px;
  }
  .ingredients h2 { font: inherit; margin: 0 0 2px 48px; }
  .ingredients ul { list-style: none; margin: 0; padding: 0; }
  .ingredients li { white-space: nowrap; }
  .ingredients li::before { content: "\2713"; margin-right: 4px; }

  .discard-note {
    left: 38px; top: 300px; width: 80px;
    font-size: 17px; line-height: 24px;
    color: var(--accent-yellow); text-align: center;
  }
  .discard-icon {
    left: 125px; top: 272px; width: 112px; height: 112px;
    background: linear-gradient(135deg, #f2f1ea, #cfcec7);
    border-radius: 8px; opacity: .85;
  }

  .instructions-frame { left: 30px; top: 400px; }
  .instructions {
    left: -100px; top: 555px; width: 490px; height: 210px;
    transform: rotate(-90deg);
    font-size: 22px; line-height: 29px;
  }

  .brand {
    left: 250px; top: 290px;
    font-size: 205px; line-height: 1;
    color: var(--brand-red);
    font-weight: 400; white-space: nowrap;
  }

  .cause {
    left: 900px; top: 362px; width: 285px;
    font-size: 28px; line-height: 36px;
  }
  .cause .emphasis {
    text-decoration: underline;
    text-decoration-color: var(--accent-yellow);
    text-decoration-thickness: 3px;
    text-underline-offset: 2px;
  }

  .product-type {
    left: 313px; top: 596px;
    font-family: "Cabin Sketch", sans-serif;
    font-weight: 700; font-size: 48px; line-height: 1.1;
    color: var(--grey-chalk); white-space: nowrap;
  }

  .tagline-frame { left: 300px; top: 690px; }
  .tagline {
    left: 330px; top: 706px; width: 340px;
    font-size: 27px; line-height: 31px; text-align: center;
  }

  .size {
    left: 440px; top: 834px;
    font-size: 22px; white-space: nowrap;
  }
  .website {
    left: 395px; top: 870px;
    font-size: 30px; white-space: nowrap;
    color: var(--accent-yellow);
  }

  .origin-frame { left: 755px; top: 635px; }
  .origin {
    left: 806px; top: 652px; width: 350px;
    font-size: 26px; line-height: 32px;
  }
  .bottle-icons {
    left: 968px; top: 790px; width: 36px; height: 30px;
    background: linear-gradient(90deg, #cfcab4, var(--accent-yellow), #cfcab4);
    border-radius: 3px;
  }
</style>
</head>
<body>
<main class="label">
  <p class="warning">Warning! To prevent fire andserious injury: Burn candle within sight. Keep away from drafts and vibrations. Keep out ofreach of children and pets. Never burn candle on or near anythig that can catch fire.</p>

  <svg class="pointer" width="30" height="150" viewBox="0 0 30 150" aria-hidden="true">
    <path d="M15 148 L15 10 M4 26 L15 6 L26 26" fill="none" stroke="var(--grey-chalk)" stroke-width="4" stroke-linecap="round"/>
  </svg>

  <h1 class="scent-name">Fizzing Mock-ree</h1>
  <svg class="scent-rule" width="520" height="20" viewBox="0 0 520 20" aria-hidden="true">
    <path d="M4 12 Q180 6 516 9" fill="none" stroke="var(--scent-green)" stroke-width="5" stroke-linecap="round"/>
  </svg>

  <section class="ingredients">
    <h2>ingredients:</h2>
    <ul>
      <li>natural soy wax</li>
      <li>100%cotton wick</li>
      <li>premium fragrance oil</li>
      <li>passion</li>
      <li>advocacy</li>
    </ul>
  </section>

  <p class="discard-note">Discard<br>or<br>Recycle</p>
  <div class="discard-icon" role="img" aria-label="Chalk figure dropping rubbish into a bin"></div>

  <svg class="instructions-frame" width="245" height="520" viewBox="0 0 245 520" aria-hidden="true">
    <path d="M6 10 Q120 4 200 8 Q236 12 236 50 L238 500 Q237 512 222 512 L12 514 Q4 513 5 500 Z" fill="none" stroke="var(--accent-yellow)" stroke-width="3"/>
  </svg>
  <p class="instructions">Burning Instructions: Trim wick to 1/4 inch before lighting. Keep candles free of foreign materials including matches and wick trimmings Only burn the candle on a level, fire resistant surface. Do not burn the candle for more than 4 hours at a time.</p>

  <h2 class="brand">BrimLO</h2>

  <p class="cause">A portion of the sales go to support <span class="emphasis">underage</span> drinking prevention programs.</p>

  <p class="product-type">Beer Bottle Candles</p>

  <svg class="tagline-frame" width="400" height="90" viewBox="0 0 400 90" aria-hidden="true">
    <path d="M6 14 L394 10 M14 10 L16 84 M384 6 L386 82 M4 80 L394 78" fill="none" stroke="var(--cream)" stroke-width="4" stroke-linecap="round"/>
  </svg>
  <p class="tagline">How Scentsible People Get Brimmed</p>

  <p class="size">11oz.e311g. /60-80 hours</p>
  <p class="website">www.brimlocandles.com</p>

  <svg class="origin-frame" width="430" height="285" viewBox="0 0 430 285" aria-hidden="true">
    <path d="M40 30 Q210 -6 400 24 Q432 40 420 140 Q410 262 300 272 Q180 284 70 268 Q8 252 10 150 Q10 50 40 30 Z" fill="none" stroke="var(--grey-chalk)" stroke-width="3"/>
  </svg>
  <p class="origin">Handcrafted in the heart of the College Triangle of North Carolina using repurposed beer bottles.</p>
  <div class="bottle-icons" role="img" aria-label="Three small bottle figures"></div>
</main>
</body>
</html>
```